Web Design Project for Communications Agency

The design I need (PSD file) is for an agency offering specialised PR and communications services for customers in the healthcare sector.

OBJECTIVES OF THE WEBSITE:
1. To promote the agency's communication services
2. To position Solène Brivard as an industry leader, an expert in healthcare PR and communications by highlighting blogposts and social media.

WHAT I NEED:
1st, I need the design for the Home Page ONLY.
Once approved, I will need the other pages designed as well. (Here is prototype that we've already developed for the Website that will guide you in the design:
http://qorvelle.net/solenebrivard/)

VISUAL INSPIRATION
We want to give this Website a "Flat Design" look. Here are some websites for inspiration :
- http://tavrolinkworks.com/#!/process
- http://www.brindlemoss.co/
- http://quellaroft.com/

Also, reuse images found on the company's current Website :
http://www.solenebrivard.com/fr/index.html

HOMEPAGE MAIN ELEMENTS:
1. Main menu : 6 sections
Accueil | Agence | Services | Approche | Publications | Contact

2. Main Call To Action (big dark rectangle in prototype):
Can be slider or just an information bloc.

3. Publications récentes :
The 4 latest blog posts must be features on the homepage (will be linked with the "Publications" section)

4. Dynamic Footer :
Contains a Chirpline feed and a Subscribe to our Newsletter feature (revecez nos publications)

OTHER PAGES (to design once Homepage is approved)
- Agence (about us)
- Services (our team)
- Approche (our approach)
- Publications (blog articles)
- Contact (Contact us)

Industry/Entity Type

Communications

Requirements
Must have
• Please refer to prototype :
http://qorvelle.net/solenebrivard/
Must have ALL features present in prototype.

Also, must reuse this picture in the design : http://solenebrivard.com/static/images/home-big-box.jpg

Finally, you will find attached the company logo.

```html
<!DOCTYPE html>
<html lang="fr">
<head>
<meta charset="utf-8">
<title>Solène Brivard — Gestion d'enjeux</title>
<link rel="stylesheet" href="https://fonts.googleapis.com/css2?family=Open+Sans:wght@300;400;600;700;800&display=swap">
<style>
  :root {
    --page-bg: #3b3b3d;
    --panel: #ffffff;
    --red: #e0393e;
    --hero-bg: #3d3d3f;
    --ink: #222222;
    --muted: #666666;
    --rule: #e2e2e2;
    --footer-ink: #e6e6e6;
    --bottom-bar: #1f1f21;
    --brand-blue: #3ab4e6;
  }
  * { box-sizing: border-box; margin: 0; padding: 0; }
  html, body { width: 678px; height: 1200px; overflow: hidden; }
  body {
    position: relative;
    background: var(--page-bg);
    font-family: "Open Sans", Arial, sans-serif;
    color: var(--ink);
  }
  .abs { position: absolute; }

  .panel { left: 90px; top: 0; width: 497px; height: 986px; background: var(--panel); }

  .social { left: 100px; top: 9px; display: flex; gap: 5px; }
  .social span { width: 8px; height: 8px; border-radius: 50%; background: var(--red); display: block; }
  .language { right: 102px; top: 8px; font-size: 6px; color: #888; display: flex; align-items: center; gap: 4px; }
  .language i { width: 9px; height: 9px; background: var(--red); border-radius: 50%; display: block; }
  .top-rule { left: 100px; top: 26px; width: 478px; height: 1px; background: var(--rule); }

  .brand { left: 90px; top: 44px; width: 497px; text-align: center; }
  .brand-name { font-size: 20px; font-weight: 400; color: var(--red); line-height: 1; letter-spacing: -0.3px; }
  .brand-tag { margin-top: 8px; font-size: 5.5px; font-weight: 700; color: #555; letter-spacing: 0.4px; line-height: 7px; }

  .main-nav { left: 100px; top: 118px; width: 478px; height: 25px; background: var(--red); display: flex; }
  .main-nav a {
    color: #fff; text-decoration: none; font-size: 6.8px; font-weight: 600;
    display: flex; align-items: center; justify-content: center;
    border-right: 1px solid rgba(0,0,0,0.12);
  }
  .main-nav a:last-child { border-right: none; }

  .hero { left: 100px; top: 144px; width: 478px; height: 122px; background: var(--hero-bg); overflow: hidden; }
  .hero h1 {
    position: absolute; left: 14px; top: 20px; width: 334px;
    font-size: 15.4px; line-height: 23px; color: #fff; font-weight: 300;
    letter-spacing: -0.45px; white-space: nowrap; z-index: 1;
  }
  .hero h1 strong { font-weight: 700; }
  .hero-btn { position: absolute; left: 14px; top: 78px; width: 55px; height: 19px; background: #f4f4f4; border: 1px solid #ccc; color: var(--red); font-size: 7.5px; display: flex; align-items: center; justify-content: center; }
  .hero-visual { position: absolute; left: 358px; top: 6px; width: 110px; height: 110px; background: radial-gradient(circle at 50% 45%, #f1f1f1 0%, #d9d9d9 45%, var(--hero-bg) 72%); }

  .section-title { left: 90px; top: 274px; width: 497px; text-align: center; font-size: 15px; font-weight: 700; color: var(--red); }

  .post { left: 105px; width: 468px; height: 160px; }
  .post-rule-left { position: absolute; left: 0; top: 0; width: 109px; height: 1px; background: var(--rule); }
  .post-rule-right { position: absolute; left: 125px; top: 0; width: 343px; height: 1px; background: var(--rule); }
  .post-title { position: absolute; left: 0; top: 15px; font-size: 10px; color: var(--ink); }
  .post-date { position: absolute; left: 0; top: 29px; font-size: 7.5px; color: var(--red); font-weight: 300; }
  .post-image { position: absolute; left: 126px; top: 17px; width: 342px; height: 80px; }
  .post-excerpt { position: absolute; left: 126px; top: 107px; width: 342px; font-size: 6.2px; line-height: 9.6px; color: var(--muted); }
  .post-btn { position: absolute; left: 126px; top: 139px; width: 40px; height: 14px; background: var(--red); color: #fff; font-size: 5.8px; font-weight: 700; display: flex; align-items: center; justify-content: center; }

  .img-docs { background: linear-gradient(100deg, #c9c3b8 0%, #e8ece8 40%, #9fd6c4 70%, #d0c2b6 100%); }
  .img-scope-blue { background: linear-gradient(100deg, #dfe8ee 0%, #b7c9d6 35%, #2c6fb3 55%, #cfdbe3 80%, #eef3f6 100%); }
  .img-scope-steel { background: linear-gradient(100deg, #2e4f8f 0%, #6f7d92 25%, #cfd2d6 55%, #e6e6e6 100%); }
  .img-ecg { background: linear-gradient(100deg, #8d9aa0 0%, #253a52 35%, #0f1e2e 65%, #08090c 100%); }

  .feed-brand { left: 98px; top: 1001px; font-size: 24px; font-weight: 800; color: var(--brand-blue); letter-spacing: -0.5px; }
  .feed-item { left: 98px; width: 236px; height: 50px; }
  .feed-avatar { position: absolute; left: 0; top: 0; width: 16px; height: 16px; background: #9a9a9a; border: 1px solid #ddd; }
  .feed-text { position: absolute; left: 25px; top: 1px; width: 211px; font-size: 6.2px; line-height: 7.6px; color: var(--footer-ink); }
  .feed-tags { position: absolute; left: 25px; top: 25px; font-size: 6.2px; color: var(--footer-ink); display: flex; gap: 10px; white-space: nowrap; }
  .feed-btn { position: absolute; left: 196px; top: 33px; width: 40px; height: 14px; background: var(--red); color: #fff; font-size: 7px; font-weight: 700; display: flex; align-items: center; justify-content: center; border-radius: 1px; }
  .feed-rule { left: 90px; top: 1098px; width: 246px; height: 1px; background: #4c4c4e; }

  .signup-title { left: 362px; top: 1011px; font-size: 12px; font-weight: 700; color: var(--red); }
  .signup-label { left: 362px; font-size: 9px; font-weight: 400; color: var(--footer-ink); }
  .signup-input { left: 363px; width: 224px; height: 22px; background: #fff; border: 1px solid #ccc; }
  .signup-btn { left: 545px; top: 1142px; width: 43px; height: 15px; background: var(--red); color: #fff; font-size: 7px; font-weight: 700; display: flex; align-items: center; justify-content: center; border-radius: 1px; }

  .bottom-bar { left: 0; top: 1173px; width: 678px; height: 27px; background: var(--bottom-bar); }
  .copyright { left: 90px; top: 1181px; font-size: 6.4px; color: #c8c8c8; }
</style>
</head>
<body>
  <div class="abs panel"></div>

  <div class="abs social"><span></span><span></span><span></span></div>
  <div class="abs language">Language: <i></i></div>
  <div class="abs top-rule"></div>

  <div class="abs brand">
    <div class="brand-name">Solène Brivard</div>
    <div class="brand-tag">GESTION D'ENJEUX<br>AFFAIRES PUBLIQUES</div>
  </div>

  <nav class="abs main-nav">
    <a style="width:76px">HOME</a>
    <a style="width:70px">AGENCE</a>
    <a style="width:72px">SERVICES</a>
    <a style="width:78px">APPROCHE</a>
    <a style="width:92px">PUBLICATIONS</a>
    <a style="width:90px">CONTACT</a>
  </nav>

  <section class="abs hero">
    <div class="hero-visual" role="img" aria-label="White cube with a red cross on its top face"></div>
    <h1><strong>Consultancy</strong> and <strong>Business Communications</strong><br>specializing in public <strong>health sector</strong>.</h1>
    <div class="hero-btn">Learn More</div>
  </section>

  <h2 class="abs section-title">Recent Publication</h2>

  <article class="abs post" style="top:306px">
    <div class="post-rule-left"></div><div class="post-rule-right"></div>
    <div class="post-title">Titre de la publication</div>
    <div class="post-date">23 juillet 2013</div>
    <div class="post-image img-docs" role="img" aria-label="Hands reviewing medical documents beside a laptop"></div>
    <p class="post-excerpt">Lorem ipsum dolor sit amet, consectetur adipisicing elit, sed do eiusmod tempor incididunt ut labore et dolore magna aliqua. Ut enim ad minim veniam, quis nostrud exercitation ullamco laboris nisi ut aliquip ex ea commodo consequat Lorem ipsum dolor sit amet, consectetur adipisicing elit.</p>
    <div class="post-btn">Learn More</div>
  </article>

  <article class="abs post" style="top:476px">
    <div class="post-rule-left"></div><div class="post-rule-right"></div>
    <div class="post-title">Titre de la publication</div>
    <div class="post-date">23 juillet 2013</div>
    <div class="post-image img-scope-blue" role="img" aria-label="Blue stethoscope lying on a printed chart"></div>
    <p class="post-excerpt">Lorem ipsum dolor sit amet, consectetur adipisicing elit, sed do eiusmod tempor incididunt ut labore et dolore magna aliqua. Ut enim ad minim veniam, quis nostrud exercitation ullamco laboris nisi ut aliquip ex ea commodo consequat Lorem ipsum dolor sit amet, consectetur adipisicing elit.</p>
    <div class="post-btn">Learn More</div>
  </article>

  <article class="abs post" style="top:647px">
    <div class="post-rule-left"></div><div class="post-rule-right"></div>
    <div class="post-title">Titre de la publication</div>
    <div class="post-date">23 juillet 2013</div>
    <div class="post-image img-scope-steel" role="img" aria-label="Steel stethoscope and pen on a medical report"></div>
    <p class="post-excerpt">Lorem ipsum dolor sit amet, consectetur adipisicing elit, sed do eiusmod tempor incididunt ut labore et dolore magna aliqua. Ut enim ad minim veniam, quis nostrud exercitation ullamco laboris nisi ut aliquip ex ea commodo consequat Lorem ipsum dolor sit amet, consectetur adipisicing elit.</p>
    <div class="post-btn">Learn More</div>
  </article>

  <article class="abs post" style="top:817px">
    <div class="post-rule-left"></div><div class="post-rule-right"></div>
    <div class="post-title">Titre de la publication</div>
    <div class="post-date">23 juillet 2013</div>
    <div class="post-image img-ecg" role="img" aria-label="Magnifying glass over a glowing heart-rate trace"></div>
    <p class="post-excerpt">Lorem ipsum dolor sit amet, consectetur adipisicing elit, sed do eiusmod tempor incididunt ut labore et dolore magna aliqua. Ut enim ad minim veniam, quis nostrud exercitation ullamco laboris nisi ut aliquip ex ea commodo consequat Lorem ipsum dolor sit amet, consectetur adipisicing elit.</p>
    <div class="post-btn">Learn More</div>
  </article>

  <div class="abs feed-brand">Chirpline</div>

  <div class="abs feed-item" style="top:1041px">
    <div class="feed-avatar" role="img" aria-label="Author avatar"></div>
    <p class="feed-text">Le Lorem Ipsum est simplement du faux texte employé dans la composition et la mise en page avant impression. Le Lorem Ipsum est le faux texte standard de.</p>
    <div class="feed-tags"><span>#free</span><span>#rebound it!</span><span>#psd</span></div>
    <div class="feed-btn">Relay</div>
  </div>
  <div class="abs feed-rule"></div>
  <div class="abs feed-item" style="top:1109px">
    <div class="feed-avatar" role="img" aria-label="Author avatar"></div>
    <p class="feed-text">Le Lorem Ipsum est simplement du faux texte employé dans la composition et la mise en page avant impression. Le Lorem Ipsum est le faux texte standard de.</p>
    <div class="feed-tags"><span>#free</span><span>#rebound it!</span><span>#psd</span></div>
    <div class="feed-btn">Relay</div>
  </div>

  <h3 class="abs signup-title">Recevez nos Publications</h3>
  <div class="abs signup-label" style="top:1038px">Votre nom</div>
  <div class="abs signup-input" style="top:1056px"></div>
  <div class="abs signup-label" style="top:1089px">Votre courriel</div>
  <div class="abs signup-input" style="top:1107px"></div>
  <div class="abs signup-btn">Subscribe</div>

  <div class="abs bottom-bar"></div>
  <div class="abs copyright">(c) Solène Brivard. Tous droits réservés.</div>
</body>
</html>
```